Business Card for beauty technology startup

Design Glimora Business Card for a Beauty, based on the website identity and colors (https://www.glimora-example.com).
Glimora is a beauty tech startup that gathers helpful product info for beauty lovers and consumers (such as availability on stores, price range and product reviews) for makeup products. The card design must be young, colorful but clean, and very modern.

Target Market(s)

woman, 15-35

Industry/Entity Type

Cosmetics

Contact Information for Business Card

Full Name, address, phone

Font styles to use
Other font styles liked:
• Advent Pro

Colors
e34297
86cfc6
ffffff
5c5c5c
e8e8e8
e667a6
b2b2b2

Requirements
Must have
• One full colored side with a creative design and another with card info
• Use Color palette: #95C5C5 and/or #D38AA5
• Use fonts: Advent Pro
• Use website identity: https://www.glimora-example.com
Nice to have
• If needed extra font: Roboto

```html
<!DOCTYPE html>
<html lang="en">
<head>
<meta charset="utf-8">
<title>Glimora Business Card</title>
<link rel="stylesheet" href="https://fonts.googleapis.com/css2?family=Advent+Pro:wght@300;400&family=Lora:ital@1&family=Roboto:wght@400&display=swap">
<style>
  :root {
    --stage: #2b2b2b;
    --rose-light: #e6bedb;
    --rose-mid: #b57f98;
    --rose-deep: #9c6a81;
    --rose-text: #c47a9b;
    --rose-band: #a8738b;
    --card-white: #fbfbfb;
    --ink: #5c5c5c;
    --white: #ffffff;
  }
  * { box-sizing: border-box; margin: 0; padding: 0; }
  html, body {
    width: 1200px; height: 900px; overflow: hidden;
    background: var(--stage);
  }
  .stage {
    width: 1200px; height: 900px;
    display: flex; flex-direction: column;
    align-items: center; justify-content: center; gap: 40px;
  }
  .card {
    position: relative;
    width: 620px; height: 354px;
    overflow: hidden;
  }
  /* Front side */
  .card--front {
    background: linear-gradient(100deg, var(--rose-light) 0%, var(--rose-mid) 45%, var(--rose-deep) 100%);
    display: flex; flex-direction: column; align-items: center; justify-content: center; gap: 22px;
  }
  .front-mark {
    width: 86px; height: 86px; border: 2px solid var(--white); border-radius: 50%;
  }
  .front-name {
    font-family: "Advent Pro", sans-serif; font-weight: 300;
    font-size: 46px; letter-spacing: 10px; color: var(--white);
    text-transform: uppercase; padding-left: 10px;
  }
  /* Back side */
  .card--back { background: var(--card-white); }
  .person {
    position: absolute; top: 36px; right: 40px; text-align: right;
    font-family: "Lora", serif; font-style: italic;
  }
  .person__name { font-size: 19px; color: var(--rose-text); }
  .person__role { font-size: 19px; color: var(--ink); }
  .brand {
    position: absolute; left: 40px; top: 128px;
    display: flex; align-items: center; gap: 16px;
  }
  .brand__mark {
    width: 48px; height: 48px; border: 1.5px solid var(--rose-text); border-radius: 50%;
  }
  .brand__name {
    font-family: "Advent Pro", sans-serif; font-weight: 300;
    font-size: 36px; letter-spacing: 6px; color: var(--rose-text);
    text-transform: uppercase;
  }
  .contacts {
    position: absolute; left: 40px; top: 196px;
    list-style: none;
    font-family: "Roboto", sans-serif; font-size: 14px; color: var(--ink);
    line-height: 20px;
  }
  .contacts li { display: flex; align-items: center; gap: 10px; }
  .contacts svg { width: 12px; height: 12px; fill: var(--rose-text); }
  .address {
    position: absolute; right: 40px; top: 214px; text-align: right;
    font-family: "Roboto", sans-serif; font-size: 14px; color: var(--ink); line-height: 19px;
  }
  .divider {
    position: absolute; left: 0; top: 290px; width: 400px; height: 1px;
    background: var(--rose-text);
  }
  .web {
    position: absolute; right: 20px; top: 278px; width: 200px; height: 24px;
    background: var(--rose-band); color: var(--white);
    font-family: "Roboto", sans-serif; font-size: 12px; letter-spacing: 1.5px;
    display: flex; align-items: center; justify-content: center;
  }
</style>
</head>
<body>
<main class="stage">
  <section class="card card--front" aria-label="Card front">
    <span class="front-mark" aria-hidden="true"></span>
    <h1 class="front-name">Glimora</h1>
  </section>

  <section class="card card--back" aria-label="Card back">
    <div class="person">
      <p class="person__name">Maya Lindqvist</p>
      <p class="person__role">CEO/Founder</p>
    </div>

    <div class="brand">
      <span class="brand__mark" aria-hidden="true"></span>
      <span class="brand__name">Glimora</span>
    </div>

    <ul class="contacts">
      <li><svg viewBox="0 0 12 12" aria-hidden="true"><path d="M1 4c0-2 2-3 5-3s5 1 5 3v1H8V3.5H4V5H1zM2 6h8l1 5H1z"/></svg>555 214 3867</li>
      <li><svg viewBox="0 0 12 12" aria-hidden="true"><path d="M3 0h6v12H3zM4 1.5v8h4v-8z"/></svg>555 730 1942</li>
      <li><svg viewBox="0 0 12 12" aria-hidden="true"><path d="M3 0h6v3H3zM1 4h10v5H9v3H3V9H1zM4 8v3h4V8z"/></svg>555 608 2175</li>
      <li><svg viewBox="0 0 12 12" aria-hidden="true"><path d="M0 2h12v1L6 7 0 3zM0 4.5l6 4 6-4V10H0z"/></svg>info@glimora-example.com</li>
    </ul>

    <address class="address" style="font-style:normal">
      1420 Willow Crest Road<br>
      Portland, Oregon 97201
    </address>

    <div class="divider" aria-hidden="true"></div>
    <div class="web">www.glimora-example.com</div>
  </section>
</main>
</body>
</html>
```